Bramwell Lodge Business Cards design with a logo

I want two Business cards designed with a very modern contemporary logo UNING 1920'S FONT STYLES with the following details

Address:
Bramwell Lodge
17 Pellham Road
Kelmsbury
KL3 2RN

Details for card 1

Name: Dermot Ashby
email: Dermot.ashby@bramwell.lodge
Tel : +61 4 1830 6094
Tel +64 21 590 3187

Details Card 2

Name: Dermot Ashby
email: Neville.osgood@bramwell.lodge
Tel : +971 52 430 9187

Bramwell lodge is a house that was built around 1880 and was used extensively in the 1920's for entertaining and parties in the arts scene, the house again will be resurrected to a modern entertainment venue

If you have any questions feel free to ask

Target Market(s)

The market for this is the young modern crowd

Industry/Entity Type

Entertainment Industry

Contact Information for Business Card

Address:
Bramwell Lodge
17 Pellham Road
Kelmsbury
KL3 2RN

Details for card 1

Name: Dermot Ashby
Tel : +61 4 1830 6094
Tel +64 21 590 3187

Details Card 2

Name: Neville Osgood
Tel : +971 52 430 9187

Logo Text

Bramwell Lodge

Font styles to use
Other font styles liked:
• 1920'S FONT STULES

Requirements
Must have
• Modern Contemporary, whilst taking into consideration the age of the house as detailed above. YOU MUT BE USING 1920'S FONT STYLES
Nice to have
• 1920'S FONT STYLES see attached image if a suggestion
Should not have
• Should not look old or dated

```html
<!DOCTYPE html>
<html lang="en">
<head>
<meta charset="utf-8">
<title>Bramwell Lodge – Business Cards</title>
<link href="https://fonts.googleapis.com/css2?family=Oswald:wght@500&family=Work+Sans:wght@400;500&display=swap" rel="stylesheet">
<style>
  :root {
    --backdrop: #2b2b2d;
    --card: #1d1d1f;
    --card-edge: #111112;
    --pattern-light: #3a3a3c;
    --pattern-dark: #1a1a1b;
    --accent: #f3e000;
    --ink: #f2f2f2;
  }
  * { margin: 0; padding: 0; box-sizing: border-box; }
  html, body { width: 1200px; height: 900px; overflow: hidden; }
  body {
    background: var(--backdrop);
    font-family: "Work Sans", sans-serif;
    color: var(--ink);
    position: relative;
  }
  .card {
    position: absolute;
    left: 250px;
    width: 700px;
    height: 400px;
    background: var(--card);
    border: 1px solid var(--card-edge);
    overflow: hidden;
  }
  .card--back { top: 40px; }
  .card--front { top: 468px; }

  .back-pattern {
    position: absolute;
    inset: 0;
    background: linear-gradient(110deg, var(--pattern-dark) 0%, #262628 45%, var(--pattern-light) 100%);
  }
  .back-brand {
    position: absolute;
    right: 40px;
    bottom: 52px;
    display: flex;
    align-items: center;
    gap: 10px;
    font-weight: 500;
    font-size: 20px;
    color: var(--accent);
  }
  .brand-square { width: 14px; height: 14px; background: var(--ink); }

  .identity {
    position: absolute;
    left: 80px;
    top: 118px;
    width: 280px;
    text-align: right;
  }
  .identity__name {
    font-family: "Oswald", sans-serif;
    font-weight: 500;
    font-size: 40px;
    letter-spacing: 0.5px;
    color: var(--accent);
    line-height: 1.1;
    text-transform: uppercase;
  }
  .identity__role { font-size: 17px; color: var(--ink); margin-top: 2px; }
  .divider {
    position: absolute;
    left: 386px;
    top: 118px;
    width: 2px;
    height: 74px;
    background: var(--accent);
  }
  .contacts {
    position: absolute;
    left: 404px;
    top: 114px;
    list-style: none;
    font-size: 16px;
    line-height: 21px;
  }
  .contacts li { display: flex; align-items: center; gap: 10px; white-space: nowrap; }
  .contacts svg { width: 12px; height: 12px; flex: none; }
  .contacts .highlight { color: var(--accent); }

  .address {
    position: absolute;
    left: 52px;
    bottom: 70px;
    display: flex;
    align-items: center;
    gap: 12px;
    font-size: 19px;
    white-space: nowrap;
  }
  .address__square { width: 14px; height: 14px; background: var(--ink); }
  .address__venue { color: var(--accent); }
  .address__postcode { margin-left: 14px; }
</style>
</head>
<body>

<section class="card card--back">
  <div class="back-pattern" role="img" aria-label="Tonal repeating brand pattern across the card back"></div>
  <div class="back-brand"><span class="brand-square"></span>Bramwell Lodge</div>
</section>

<section class="card card--front">
  <div class="identity">
    <h1 class="identity__name">Dermot Ashby</h1>
    <p class="identity__role">Director</p>
  </div>
  <div class="divider"></div>
  <ul class="contacts">
    <li>
      <svg viewBox="0 0 12 12"><path d="M2.5 1l2 2.2-1 1.3a7 7 0 0 0 4 4l1.3-1 2.2 2-1.3 1.5C5 11 1 7 1 2.3z" fill="#f3e000"/></svg>
      <span>+61 4 1830 6094</span>
    </li>
    <li>
      <svg viewBox="0 0 12 12"><rect x="1" y="2" width="10" height="3" rx="1.5" fill="#f3e000"/><rect x="3" y="6" width="6" height="5" fill="#f3e000"/></svg>
      <span>+64 21 590 3187</span>
    </li>
    <li>
      <svg viewBox="0 0 12 12"><rect x="1" y="2.5" width="10" height="7" fill="none" stroke="#f3e000" stroke-width="1.2"/><path d="M1 2.5l5 4 5-4" fill="none" stroke="#f3e000" stroke-width="1.2"/></svg>
      <span>Dermot.ashby@bramwell.lodge</span>
    </li>
    <li>
      <svg viewBox="0 0 12 12"><circle cx="6" cy="6" r="5" fill="none" stroke="#f3e000" stroke-width="1.1"/><ellipse cx="6" cy="6" rx="2.2" ry="5" fill="none" stroke="#f3e000" stroke-width="1"/><path d="M1 6h10" stroke="#f3e000" stroke-width="1"/></svg>
      <span>www.<span class="highlight">bramwelllodge</span>.com</span>
    </li>
  </ul>
  <p class="address">
    <span class="address__square"></span>
    <span><span class="address__venue">Bramwell Lodge,</span> 17 Pellham Road Kelmsbury<span class="address__postcode">KL3 2RN</span></span>
  </p>
</section>

</body>
</html>
```